IT Company requires new Business Card design.

Over the years we have had a few different business card designs. We are now due for new cards across the board for all staff. We felt this would be a good time to start fresh with a new design. Our traditional card simply had our details on the front, and a list of services on the back. We don't particularly need the list of services, we have had cards where the only thing on the rear of the card was our logo.
Feel free to be creative, we would like our tag line "Complete IT Management" to appear at some point, doesn't necessarily have to be with the logo.
I have attached samples and drafts of various previous cards we have used over the years.

```html
<!DOCTYPE html>
<html lang="en">
<head>
<meta charset="utf-8">
<title>Harbor Systems – Business Card</title>
<link href="https://fonts.googleapis.com/css2?family=Open+Sans:wght@400;600;700;800&display=swap" rel="stylesheet">
<style>
  :root {
    --page-bg: #d8d3cd;
    --card-bg: #ffffff;
    --slate: #5f6d77;
    --slate-dark: #56636c;
    --ink: #2f3335;
    --muted: #59636a;
    --shadow: rgba(40, 30, 20, 0.28);
  }
  html, body {
    margin: 0;
    padding: 0;
    width: 1034px;
    height: 1200px;
    overflow: hidden;
    background: var(--page-bg);
    font-family: "Open Sans", Arial, sans-serif;
  }
  .canvas {
    position: relative;
    width: 1034px;
    height: 1200px;
  }
  .card {
    position: absolute;
    left: 72px;
    width: 902px;
    height: 512px;
    background: var(--card-bg);
    border-radius: 44px;
    box-shadow: 0 4px 14px var(--shadow);
    overflow: hidden;
  }
  .card--front { top: 69px; }
  .card--back  { top: 632px; }

  /* Front */
  .accent-bar {
    position: absolute;
    left: 0;
    top: 48px;
    width: 17px;
    height: 42px;
    background: var(--slate);
  }
  .person-name {
    position: absolute;
    left: 48px;
    top: 50px;
    margin: 0;
    font-size: 29px;
    font-weight: 700;
    color: var(--slate);
    line-height: 1;
  }
  .person-role {
    position: absolute;
    left: 48px;
    top: 88px;
    margin: 0;
    font-size: 22px;
    color: var(--muted);
    line-height: 1;
  }
  .address {
    position: absolute;
    left: 48px;
    top: 156px;
    margin: 0;
    font-style: normal;
    font-size: 22px;
    line-height: 31px;
    color: var(--ink);
  }
  .contact-list {
    position: absolute;
    left: 48px;
    top: 252px;
    margin: 0;
    padding: 0;
    list-style: none;
    font-size: 21.5px;
    color: var(--ink);
  }
  .contact-list li {
    display: flex;
    align-items: center;
    height: 36.5px;
  }
  .contact-icon {
    width: 22px;
    height: 22px;
    margin-right: 13px;
    flex: none;
  }
  .tagline {
    position: absolute;
    left: 48px;
    top: 446px;
    margin: 0;
    font-size: 22px;
    font-weight: 700;
    color: var(--slate);
  }
  .brand-lockup {
    position: absolute;
    left: 448px;
    top: 162px;
    display: flex;
    align-items: center;
    gap: 22px;
  }
  .brand-square {
    width: 98px;
    height: 98px;
    background: var(--slate);
    flex: none;
  }
  .brand-name {
    margin: 0;
    font-size: 50px;
    font-weight: 800;
    line-height: 0.98;
    color: var(--slate);
    letter-spacing: 0.5px;
  }

  /* Back */
  .brand-mark-large {
    position: absolute;
    left: 0;
    right: 0;
    top: 110px;
    display: flex;
    flex-direction: column;
    align-items: center;
    gap: 26px;
  }
  .brand-mark-large .brand-square {
    width: 150px;
    height: 150px;
  }
  .brand-mark-large .brand-name {
    font-size: 56px;
    line-height: 1;
  }
  .back-url {
    position: absolute;
    left: 0;
    right: 0;
    top: 462px;
    margin: 0;
    text-align: center;
    font-size: 25px;
    letter-spacing: 3px;
    color: var(--ink);
  }
</style>
</head>
<body>
<main class="canvas">

  <section class="card card--front" aria-label="Card front">
    <div class="accent-bar"></div>
    <h1 class="person-name">Mark Ellison</h1>
    <p class="person-role">Operation Manager</p>

    <address class="address">Unit 7 22 Marlow Street<br>Bibra Lake WA 6163</address>

    <ul class="contact-list">
      <li>
        <svg class="contact-icon" viewBox="0 0 24 24" aria-hidden="true">
          <circle cx="12" cy="12" r="10.5" fill="none" stroke="var(--ink)" stroke-width="1.6"/>
          <path d="M8.5 6.5c-1 1-1 3 .8 5.6 1.8 2.6 3.9 4.3 5.6 4.6l1.3-1.6-2-1.6-1 .9c-.9-.5-2.3-2-2.8-3.1l.9-1-1.4-2.2z" fill="var(--ink)"/>
        </svg>
        08 9555 0147
      </li>
      <li>
        <svg class="contact-icon" viewBox="0 0 24 24" aria-hidden="true">
          <rect x="7" y="2" width="10" height="20" rx="1.5" fill="var(--ink)"/>
          <rect x="8.6" y="4.5" width="6.8" height="7" fill="#fff"/>
          <rect x="8.6" y="13.5" width="6.8" height="6" fill="#9aa3a9"/>
        </svg>
        0400 118 629
      </li>
      <li>
        <svg class="contact-icon" viewBox="0 0 24 24" aria-hidden="true">
          <rect x="7" y="3" width="10" height="7" fill="none" stroke="var(--ink)" stroke-width="1.6"/>
          <rect x="2" y="10" width="20" height="9" rx="1.5" fill="var(--ink)"/>
          <rect x="6" y="16" width="12" height="5" fill="var(--ink)"/>
        </svg>
        08 9555 0148
      </li>
      <li>
        <svg class="contact-icon" viewBox="0 0 24 24" aria-hidden="true">
          <rect x="2" y="6" width="20" height="13" rx="1" fill="var(--ink)"/>
          <path d="M3 7l9 7 9-7" fill="none" stroke="#fff" stroke-width="1.6"/>
        </svg>
        mark@harborsystems.com.au
      </li>
      <li>
        <svg class="contact-icon" viewBox="0 0 24 24" aria-hidden="true">
          <g fill="none" stroke="var(--ink)" stroke-width="1.6">
            <circle cx="12" cy="12" r="9.5"/>
            <ellipse cx="12" cy="12" rx="4" ry="9.5"/>
            <path d="M2.5 12h19M4 7.5h16M4 16.5h16"/>
          </g>
        </svg>
        www.harborsystems.com.au
      </li>
    </ul>

    <p class="tagline">Complete IT Management</p>

    <div class="brand-lockup">
      <div class="brand-square" aria-hidden="true"></div>
      <p class="brand-name">HARBOR<br>SYSTEMS</p>
    </div>
  </section>

  <section class="card card--back" aria-label="Card back">
    <div class="brand-mark-large">
      <div class="brand-square" aria-hidden="true"></div>
      <p class="brand-name">HARBOR SYSTEMS</p>
    </div>
    <p class="back-url">www.harborsystems.com.au</p>
  </section>

</main>
</body>
</html>
```